Wedding Invitation to be used digitally

Design of a Wedding Invitation.
It will be used digitally by whatsapp, so the file format and image size should be appropriate. We don´t intend to print.
Word file with the text contents as attachment. This is REALLY just the text and the main sequencial order of the information that should appear in the invitation.
However, ALL criativity is welcome ofcourse in terms of organization of the information in the paper, font, uppercase and lowercase, numbers and their format, dates and their format, drawings, logo, etc etc

Target Market(s)

family and friends

Requirements
Must have
• A logo at the top with the capitals of our name - R and T
Nice to have
• Should be elegant

```html
<!DOCTYPE html>
<html lang="en">
<head>
<meta charset="utf-8">
<title>Wedding Invitation – Raquel &amp; Tomás</title>
<link rel="stylesheet" href="https://fonts.googleapis.com/css2?family=Playfair+Display:wght@400;500&display=swap">
<style>
  :root {
    --backdrop: #efebec;
    --tile-navy: #284b80;
    --tile-light: #b9c9df;
    --gold: #ae9160;
    --ink: #2d2c2c;
    --amp-blue: #cfd8e8;
    --paper: #ffffff;
  }
  * { margin: 0; padding: 0; box-sizing: border-box; }
  html, body {
    width: 1200px; height: 854px; overflow: hidden;
    background: var(--backdrop);
    font-family: "Playfair Display", Georgia, serif;
    color: var(--ink);
  }
  .invitation {
    position: absolute; left: 361px; top: 95px; width: 458px; height: 647px;
  }
  .tile-border {
    position: absolute; inset: 0;
    background: radial-gradient(circle at 50% 50%, var(--tile-light) 0%, var(--tile-navy) 140%);
    background-color: var(--tile-navy);
  }
  .card {
    position: absolute; left: 36px; top: 47px; width: 388px; height: 554px;
    background: var(--paper);
    border: 2px solid var(--gold);
  }
  .line {
    position: absolute; left: 0; width: 100%; text-align: center; white-space: nowrap;
  }
  .monogram {
    top: 40px; font-size: 70px; font-weight: 400; color: var(--gold); line-height: 1;
  }
  .ampersand {
    top: 179px; font-size: 112px; color: var(--amp-blue); line-height: 1;
  }
  .spaced { letter-spacing: 2.4px; font-size: 11.5px; }
  .together { top: 175px; }
  .name { font-size: 32px; line-height: 1; font-weight: 400; }
  .name-one { top: 196px; }
  .name-two { top: 267px; }
  .invite { top: 324px; font-size: 10.5px; letter-spacing: 1.6px; }
  .rule {
    position: absolute; left: 163px; top: 350px; width: 62px; height: 1.5px; background: var(--gold);
  }
  .date { top: 361px; font-size: 14.5px; line-height: 18px; }
  .details { font-size: 9.6px; line-height: 12px; }
  .chapel { top: 414px; }
  .reception { top: 450px; }
  .venue { top: 474px; }
  .rsvp { top: 528px; font-size: 11px; letter-spacing: 1.4px; }
</style>
</head>
<body>
  <main class="invitation">
    <div class="tile-border" role="img" aria-label="Blue and white Portuguese azulejo tile pattern border"></div>
    <section class="card">
      <div class="line monogram">R&amp;T</div>
      <div class="line ampersand" aria-hidden="true">&amp;</div>
      <p class="line spaced together">TOGETHER WITH THEIR FAMILIES</p>
      <h1 class="line name name-one">RAQUEL MOURA</h1>
      <h1 class="line name name-two">TOMÁS FERREIRA</h1>
      <p class="line invite">INVITE YOU TO THEIR WEDDING CELEBRATION</p>
      <div class="rule"></div>
      <p class="line date">SUNDAY, JULY 28, 2024<br>AT 11h30</p>
      <p class="line details chapel">CAPELA DE SANTA LUZIA | ALVORADA<br>(PARKING – MARINA DA ALVORADA OR PARQUE CAIS NORTE ALVORADA)</p>
      <p class="line details reception">RECEPTION TO FOLLOW</p>
      <p class="line details venue">AT<br>HOTEL FORTE DA PRAIA GRANDE | ALVORADA<br>(PARKING – ON SITE)</p>
      <p class="line rsvp">RSVP BY 20TH JULY</p>
    </section>
  </main>
</body>
</html>
```